Animal Eye Clinic needs a Business card

We are a new veterinary ophthalmology practice (Ridgeline Pet Vision Care) and we need a business card designed. We only see animal eyes - we are not a regular veterinary clinic. We already have a logo. We are looking for a professional, good looking business card to hand out to our clients. We are looking for something simple but professional and contemporary. Our logo is likely the only picture/graphic that needs to be on the card.
Updates

Contact Information for Business Card

Delia Vossman, BSc, DVM, PhD, DECVO
Veterinary Eye Specialist

Phone: 250.418.3927
Email: ridgelinepetvisioncare@mailbox-example.net
Website: ridgelinepetvisioncare-example.net
Address: 1874 Thornbury Rd
Larchmere, AB, V1X 4M9

Colors

Designer to choose colors to be used in the design.

Requirements
Must have
• Our logo (attached)

```html
<!DOCTYPE html>
<html lang="en">
<head>
<meta charset="utf-8">
<title>Ridgeline Pet Vision Care – Business Card</title>
<link rel="stylesheet" href="https://fonts.googleapis.com/css2?family=Roboto:wght@300;400;500;700&display=swap">
<style>
  :root {
    --teal: #13a9b6;
    --teal-dark: #0b8f9c;
    --grey: #9a9c9e;
    --grey-light: #c4c6c8;
    --paper: #f7f8f8;
    --ink: #5a5d60;
    --backdrop: #e4e6e7;
    --faint: #eceff0;
  }
  * { margin: 0; padding: 0; box-sizing: border-box; }
  html, body { width: 1200px; height: 780px; overflow: hidden; }
  body {
    background: var(--backdrop);
    font-family: "Roboto", Arial, sans-serif;
    display: flex;
    align-items: center;
    justify-content: center;
    gap: 30px;
  }
  .card {
    position: relative;
    width: 560px;
    height: 320px;
    border-radius: 16px;
    background: var(--paper);
    overflow: hidden;
    box-shadow: 0 2px 0 var(--teal-dark), 0 6px 18px rgba(0,0,0,0.12);
  }
  .card-art { position: absolute; inset: 0; }

  /* Front */
  .contact { position: absolute; left: 32px; top: 58px; color: var(--ink); }
  .contact-name { font-size: 17px; color: var(--teal); font-weight: 300; letter-spacing: -0.1px; }
  .contact-name strong { font-weight: 700; }
  .contact-title { font-size: 12.5px; font-weight: 400; margin-top: 3px; }
  .contact-address { font-size: 12.5px; line-height: 1.45; margin-top: 24px; }
  .contact-lines { list-style: none; margin-top: 12px; font-size: 11px; line-height: 1.75; }
  .contact-lines li { display: flex; align-items: center; gap: 7px; }
  .contact-lines svg { width: 11px; height: 11px; flex: none; }

  .band-brand {
    position: absolute;
    left: 520px; top: 160px;
    transform: translate(-50%, -50%) rotate(-90deg);
    color: #fff;
    font-weight: 500;
    text-align: center;
    white-space: nowrap;
  }
  .band-brand .brand-top { font-size: 11px; letter-spacing: 7px; }
  .band-brand .brand-bottom { font-size: 15px; letter-spacing: 0.5px; margin-top: 2px; }

  /* Back */
  .brand-lockup {
    position: absolute; left: 50%; top: 50%;
    transform: translate(-50%, -50%);
    display: flex; align-items: center; gap: 14px;
    color: var(--teal);
    font-weight: 500;
  }
  .brand-dot { width: 34px; height: 34px; border-radius: 50%; background: var(--teal); }
  .brand-lockup .brand-top { font-size: 13px; letter-spacing: 9px; }
  .brand-lockup .brand-bottom { font-size: 22px; letter-spacing: 0.5px; margin-top: 2px; }
</style>
</head>
<body>

  <section class="card card-front" aria-label="Business card front">
    <svg class="card-art" viewBox="0 0 560 320" aria-hidden="true">
      <circle cx="330" cy="86" r="66" fill="var(--faint)"/>
      <path d="M300 320 Q390 160 450 0 L462 0 Q405 165 326 320 Z" fill="var(--grey)"/>
      <path d="M350 320 Q430 160 478 0 L560 0 L560 320 Z" fill="var(--teal)"/>
    </svg>

    <div class="contact">
      <p class="contact-name"><strong>Delia Vossman</strong>, BSc, DVM, PhD, DECVO</p>
      <p class="contact-title">Veterinary Eye Specialist</p>
      <p class="contact-address">1874 Thornbury Rd<br>Larchmere, AB, V1X 4M9</p>
      <ul class="contact-lines">
        <li>
          <svg viewBox="0 0 12 12"><rect x="2" y="0.5" width="8" height="11" rx="1.5" fill="none" stroke="var(--teal)" stroke-width="1.2"/><line x1="5" y1="9.5" x2="7" y2="9.5" stroke="var(--teal)" stroke-width="1"/></svg>
          250.418.3927
        </li>
        <li>
          <svg viewBox="0 0 12 12"><rect x="0.5" y="2" width="11" height="8" fill="var(--teal)"/><path d="M0.5 2 L6 6.5 L11.5 2" fill="none" stroke="#fff" stroke-width="1"/></svg>
          ridgelinepetvisioncare@mailbox-example.net
        </li>
        <li>
          <svg viewBox="0 0 12 12"><circle cx="6" cy="6" r="5.5" fill="var(--teal)"/><ellipse cx="6" cy="6" rx="2.3" ry="5.3" fill="none" stroke="#fff" stroke-width="0.8"/><line x1="0.5" y1="6" x2="11.5" y2="6" stroke="#fff" stroke-width="0.8"/></svg>
          ridgelinepetvisioncare-example.net
        </li>
      </ul>
    </div>

    <div class="band-brand">
      <p class="brand-top">RIDGELINE</p>
      <p class="brand-bottom">PET VISION CARE</p>
    </div>
  </section>

  <section class="card card-back" aria-label="Business card back">
    <svg class="card-art" viewBox="0 0 560 320" aria-hidden="true">
      <path d="M0 0 L560 0 L560 30 Q300 55 0 95 Z" fill="var(--teal)"/>
      <path d="M0 108 Q300 65 560 38 L560 46 Q300 78 0 120 Z" fill="var(--grey-light)"/>
      <path d="M560 200 Q260 242 0 272 L0 279 Q260 252 560 211 Z" fill="var(--grey)"/>
      <path d="M0 320 L560 320 L560 225 Q260 265 0 290 Z" fill="var(--teal)"/>
    </svg>

    <div class="brand-lockup">
      <span class="brand-dot"></span>
      <div>
        <p class="brand-top">RIDGELINE</p>
        <p class="brand-bottom">PET VISION CARE</p>
      </div>
    </div>
  </section>

</body>
</html>
```